Business card design for a dynamic IT consulting company

We need a business card design for a young firm, specialized in the Telecommunications/Consulting industry. The name of the company is Quindor and Partners Business Consulting Ltd. (Short name: Quindor and Partnes)
Quindor = solve read reverse, so we aim to be uncomplicated and solution-oriented. The small pipe in our logo is also related to the word solve. So we need a new business card design, which is simple, eye catching and something non traditional (I would probably prefer a square shaped design rather than a rectangle, but open for suggestions). Attached our logo.

Target Market(s)

Usually our customers are Tier1 Telecoms providers (Q-Netra, Palorix, etc) and their executives.

Industry/Entity Type

Business

Contact Information for Business Card

Name: Bence Tolnavari
Email: b.tolnavari@quindor.hu
Web: www.quindor.hu
Mobile: +36 30 518 2769
Title: Managing Director

Optional:
Company name: Quindor and Partners Ltd.
Address: 1087 Budapest, Tolvenka str. 28/C, Hungary

Font styles to use
Other font styles liked:
• helveticaneue_medium, Prime Regular are used now.

Colors

Designer to choose colors to be used in the design.

Requirements
Must have
• I would like to have a 2 sided design.
Nice to have
• I thought if we make the logo a bit bigger (without the company name), that could go to the back with the company name below. I though, if the pipe in the logo is somehow touchable on the business card, would be nice and unique.

```html
<!DOCTYPE html>
<html lang="en">
<head>
<meta charset="utf-8">
<title>Quindor &amp; Partners – Business Card</title>
<link rel="stylesheet" href="https://fonts.googleapis.com/css2?family=Arimo:wght@400;700&display=swap">
<style>
  :root {
    --backdrop: #584635;
    --card-front: #f4f4f3;
    --card-back: #5c5d60;
    --ink: #4f5053;
    --ink-soft: #5a5b5e;
    --accent-blue: #1a93d2;
    --accent-magenta: #b3278e;
    --white: #ffffff;
  }
  * { margin: 0; padding: 0; box-sizing: border-box; }
  html, body {
    width: 1200px; height: 960px; overflow: hidden;
    background: var(--backdrop);
    font-family: "Arimo", Arial, sans-serif;
  }
  .card {
    position: absolute; top: 309px;
    width: 342px; height: 343px;
  }
  .card--front { left: 235px; background: var(--card-front); color: var(--ink); }
  .card--back { left: 623px; background: var(--card-back); }

  .wordmark {
    position: absolute; right: 37px; top: 44px;
    font-size: 25px; font-weight: 400; color: var(--ink-soft);
    letter-spacing: -0.3px; line-height: 1;
  }
  .contact { position: absolute; right: 37px; top: 114px; text-align: right; }
  .contact__name {
    font-size: 19px; font-weight: 700; color: var(--accent-blue);
    letter-spacing: 0.2px; line-height: 24px;
  }
  .contact__title { font-size: 15px; line-height: 20px; letter-spacing: 0.3px; }
  .contact__block { font-size: 14px; line-height: 18.5px; margin-top: 12px; }
  .contact__block + .contact__block { margin-top: 10px; }

  .web-band {
    position: absolute; left: 80px; right: 0; top: 297px; height: 26px;
    background: var(--ink-soft); color: var(--white);
    font-size: 14px; letter-spacing: 2.4px;
    text-align: right; padding-right: 36px; line-height: 26px;
  }
  .band-marker {
    position: absolute; left: 50px; top: 304px;
    width: 12px; height: 12px; background: var(--accent-magenta);
  }

  .back-marker {
    position: absolute; left: 164px; top: 116px;
    width: 16px; height: 16px; background: var(--accent-blue);
  }
  .back-wordmark {
    position: absolute; left: 0; right: 0; top: 190px;
    text-align: center; color: var(--white);
    font-size: 30px; font-weight: 400; letter-spacing: -0.3px; line-height: 1;
  }
</style>
</head>
<body>
  <section class="card card--front" aria-label="Card front">
    <div class="wordmark">Quindor &amp; Partners</div>
    <div class="contact">
      <p class="contact__name">BENCE TOLNAVARI</p>
      <p class="contact__title">MANAGING DIRECTOR</p>
      <p class="contact__block">Quindor and Partners Ltd.<br>1087 Budapest<br>Tolvenka str. 28/C, Hungary</p>
      <p class="contact__block">Mobile: +36 30 518 2769<br>Email: b.tolnavari@quindor.hu</p>
    </div>
    <span class="band-marker"></span>
    <div class="web-band">www.quindor.hu</div>
  </section>

  <section class="card card--back" aria-label="Card back">
    <span class="back-marker"></span>
    <div class="back-wordmark">Quindor &amp; Partners</div>
  </section>
</body>
</html>
```